Brightfield Ventures Inc. Letterhead

Creation of attractive and eye catching letterhead for a business start-up for the construction industry. Letterhead must relate to construction, but avoid standard hammer and tools in the design.

I forgot to add some details, sorry about that. Some pertinent info: Ph: 916-555-0187 brightfieldventures.example 448 Willowmere Ave, Ste 210 Folsom, CA 95999 info@brightfieldventures.example not sure if slogan should be in there" “Connecting construction professionals to create a purpose driven industry.” must be able to be used in word. Thanks!

```html
<!DOCTYPE html>
<html lang="en">
<head>
<meta charset="utf-8">
<title>Brightfield Ventures Inc. Letterhead</title>
<link rel="stylesheet" href="https://fonts.googleapis.com/css2?family=Open+Sans:wght@400;600;700&display=swap">
<style>
  :root {
    --backdrop: #e4e4e5;
    --paper: #f8f8f8;
    --navy: #3d3463;
    --red: #c3262e;
    --ink: #2b2b2b;
    --body-ink: #3a3a3a;
    --faint: rgba(61, 52, 99, 0.05);
  }
  * { box-sizing: border-box; margin: 0; padding: 0; }
  html, body { width: 1200px; height: 945px; overflow: hidden; }
  body {
    background: var(--backdrop);
    font-family: "Open Sans", Arial, sans-serif;
    display: flex; align-items: center; justify-content: center;
  }
  .letterhead {
    position: relative;
    width: 620px; height: 877px;
    background: var(--paper);
    box-shadow: 0 6px 22px rgba(0,0,0,0.12);
    overflow: hidden;
  }
  .brand {
    position: absolute; top: 46px; left: 52px;
    display: flex; align-items: center; gap: 8px;
  }
  .brand-mark { width: 14px; height: 14px; background: var(--red); }
  .brand-name {
    font-size: 15px; font-weight: 700; color: var(--navy);
    letter-spacing: 0.04em; text-transform: uppercase;
  }
  .backdrop-name {
    position: absolute; top: 350px; left: 0; width: 100%;
    text-align: center; font-size: 96px; font-weight: 700;
    color: var(--faint); letter-spacing: 0.02em;
  }
  .letter {
    position: absolute; top: 140px; left: 62px; right: 70px;
    color: var(--body-ink);
  }
  .salutation { font-size: 14px; font-weight: 700; color: var(--ink); margin-bottom: 12px; }
  .letter p { font-size: 11.5px; line-height: 1.45; margin-bottom: 16px; }
  .signature {
    position: absolute; top: 650px; left: 80px;
    width: 130px; height: 46px; background: #ececec; border-radius: 4px;
  }
  .contact {
    position: absolute; bottom: 30px; left: 96px;
    display: flex; gap: 18px; font-size: 9.5px; color: var(--ink); line-height: 1.5;
  }
  .contact-address { font-style: normal; white-space: nowrap; }
  .contact-lines div { display: flex; align-items: center; gap: 5px; white-space: nowrap; }
  .contact svg { width: 9px; height: 9px; fill: var(--navy); }
  .website {
    position: absolute; bottom: 30px; right: 22px;
    font-size: 9.5px; color: var(--ink); white-space: nowrap;
  }
  .footer-band { position: absolute; left: 0; bottom: 0; width: 100%; height: 22px; }
</style>
</head>
<body>
  <main class="letterhead">
    <header class="brand">
      <span class="brand-mark"></span>
      <span class="brand-name">Brightfield Ventures Inc.</span>
    </header>

    <div class="backdrop-name" aria-hidden="true">Brightfield</div>

    <section class="letter">
      <h2 class="salutation">Dear Mr. Harlow,</h2>
      <p>Lorem Ipsum is simply dummy text of the printing and typesetting industry. Lorem Ipsum has been the industry's standard dummy text ever since the 1500s, when an unknown printer took a galley of type and scrambled it to make a type specimen book. It has survived not only five centuries, but also the leap into electronic typesetting, remaining essentially unchanged.</p>
      <p>The standard chunk of Lorem Ipsum used since the 1500s is reproduced below for those interested. Sections 1.10.32 and 1.10.33 from "de Finibus Bonorum et Malorum" by Verrius are also reproduced in their exact original form, accompanied by English versions from the 1914 translation by H. Pellam.</p>
      <p>Lorem Ipsum is simply dummy text of the printing and typesetting industry. Lorem Ipsum has been the industry's standard dummy text ever since the 1500s, when an unknown printer took a galley of type and scrambled it to make a type specimen book. It has survived not only five centuries, but also the leap into electronic typesetting, remaining essentially unchanged. It was popularised in the</p>
      <p>The standard chunk of Lorem Ipsum used since the 1500s is reproduced below for those interested. Sections 1.10.32 and 1.10.33 from "de Finibus Bonorum et Malorum" by Verrius are also reproduced in their exact original form, accompanied by English versions from the 1914 translation by H. Pellam.</p>
      <p>The standard chunk of Lorem Ipsum used since the 1500s is reproduced below for those interested. Sections 1.10.32 and 1.10.33 from "de Finibus Bonorum et Malorum" by Verrius are also reproduced in their exact original form.</p>
    </section>

    <div class="signature" role="img" aria-label="Handwritten signature"></div>

    <footer>
      <div class="contact">
        <address class="contact-address">448 Willowmere Ave, Ste 210,<br>Folsom, CA 95999</address>
        <div class="contact-lines">
          <div><svg viewBox="0 0 10 10"><path d="M2 0.5 L3.6 0.5 L4.2 3 L3 3.8 Q4 6 6.2 7 L7 5.8 L9.5 6.4 L9.5 8 Q9.5 9.5 8 9.5 Q1 9 0.5 2 Q0.5 0.5 2 0.5Z"/></svg>916-555-0187</div>
          <div><svg viewBox="0 0 10 10"><path d="M0.5 2 H9.5 V8 H0.5Z M0.5 2 L5 5.5 L9.5 2" fill="none" stroke="#3d3463" stroke-width="1"/></svg>info@brightfieldventures.example</div>
        </div>
      </div>
      <div class="website">brightfieldventures.example</div>
      <svg class="footer-band" viewBox="0 0 620 22" preserveAspectRatio="none" aria-hidden="true">
        <rect x="0" y="0" width="620" height="22" fill="#3d3463"/>
        <polygon points="468,0 620,0 620,22 460,22" fill="#c3262e"/>
        <polygon points="446,0 452,0 444,22 438,22" fill="#c3262e"/>
        <polygon points="456,0 462,0 454,22 448,22" fill="#c3262e"/>
        <polygon points="440,0 446,0 438,22 432,22" fill="#f8f8f8"/>
        <polygon points="452,0 456,0 448,22 444,22" fill="#f8f8f8"/>
        <polygon points="462,0 468,0 460,22 454,22" fill="#f8f8f8"/>
      </svg>
    </footer>
  </main>
</body>
</html>
```